The book is called "Distance Racing Blueprints: An In-Depth Manual for Achieving Your Peak Race Day - Featuring Schedules, Counsel and Target-Reaching Pointers "

It is a 6" x 9" book with 205 pages. This is an advanced book for runners who have been running and trying to hit their marathon goals, but haven't been able to do so. This needs to portray a professional coaching image and high performing athlete.

I have running photos of myself running marathons if you thought that was the route to take, but I'm open to your creative influence.

```html
<!DOCTYPE html>
<html lang="en">
<head>
<meta charset="utf-8">
<title>Distance Racing Blueprints – Book Cover Wrap</title>
<link rel="stylesheet" href="https://fonts.googleapis.com/css2?family=Bebas+Neue&family=Oswald:wght@300;500&family=Arimo&display=swap">
<style>
  :root {
    --bg: #2b2b2b;
    --paper: #ffffff;
    --accent: #22bfe5;
    --ink: #0a0a0a;
    --body-ink: #1a1a1a;
  }
  * { box-sizing: border-box; margin: 0; padding: 0; }
  html, body { width: 1200px; height: 1200px; overflow: hidden; background: var(--bg); }
  .wrap {
    position: absolute; left: 40px; top: 204px;
    width: 1120px; height: 792px;
    display: flex; background: var(--paper);
  }
  .title-display { font-family: "Bebas Neue", "Oswald", sans-serif; line-height: 1; }
  .sub { font-family: "Oswald", sans-serif; font-weight: 300; text-transform: uppercase; color: #333; text-align: center; }
  .blue { color: var(--accent); }
  .black { color: var(--ink); }

  /* Back cover */
  .back { width: 528px; height: 100%; padding: 62px 48px 0 49px; }
  .back-title { font-size: 45px; white-space: nowrap; text-align: center; letter-spacing: 0.2px; }
  .back-sub { font-size: 15px; line-height: 22px; margin-top: 20px; }
  .blurb {
    font-family: "Arimo", Arial, sans-serif; font-size: 13.4px; line-height: 18.35px;
    color: var(--body-ink); text-align: justify; margin-top: 22px;
  }
  .blurb p + p { margin-top: 18px; }

  /* Spine */
  .spine {
    width: 64px; height: 100%; background: var(--accent);
    display: flex; flex-direction: column; align-items: center; padding-top: 36px;
  }
  .spine-title { writing-mode: vertical-rl; color: #fff; font-size: 46px; white-space: nowrap; }
  .spine-author {
    writing-mode: vertical-rl; color: #fff; font-family: "Oswald", sans-serif; font-weight: 500;
    font-size: 24px; letter-spacing: 1px; margin-top: 52px; white-space: nowrap;
  }

  /* Front cover */
  .front { position: relative; width: 528px; height: 100%; overflow: hidden; }
  .author {
    position: absolute; top: 36px; width: 100%; text-align: center;
    font-family: "Oswald", sans-serif; font-weight: 500; font-size: 23px; letter-spacing: 1px; color: var(--ink);
  }
  .front-title { position: absolute; top: 86px; width: 100%; text-align: center; z-index: 2; }
  .front-title span { display: block; font-size: 128px; line-height: 97px; }
  .front-sub { position: absolute; top: 382px; width: 100%; font-size: 18px; line-height: 24px; z-index: 2; }
  .photo {
    position: absolute; left: 0; bottom: 0; width: 100%; height: 340px; z-index: 1;
    background:
      linear-gradient(180deg, #ffffff 0%, rgba(255,255,255,0.6) 18%, rgba(255,255,255,0) 40%),
      linear-gradient(180deg, #cfd9c4 0%, #a9bc99 30%, #d9a583 55%, #6cb8d8 75%, #3d6fb0 100%);
  }
</style>
</head>
<body>
  <div class="wrap">
    <section class="back">
      <h2 class="back-title title-display"><span class="blue">DISTANCE RACING</span> <span class="black">BLUEPRINTS</span></h2>
      <p class="back-sub sub">An in-depth manual for achieving your peak race day<br>featuring schedules, counsel and target-reaching pointers</p>
      <div class="blurb">
        <p>Lorem ipsum dolor sit amet, consectetur adipiscing elit, sed do eiusmod tempor incididunt ut labore et dolore magna aliqua. Quis ipsum suspendisse ultrices gravida. Risus commodo viverra maecenas accumsan lacus vel facilisis. Lorem ipsum dolor sit amet, consectetur adipiscing elit, sed do eiusmod tempor incididunt ut labore et dolore magna aliqua. Quis ipsum suspendisse ultrices gravida. Risus commodo viverra maecenas accumsan lacus vel facilisis. Lorem ipsum dolor sit amet, consectetur adipiscing elit, sed do eiusmod tempor incididunt ut labore et dolore magna aliqua. Quis ipsum suspendisse ultrices gravida. Risus commodo viverra maecenas accumsan lacus vel facilisis. Lorem ipsum dolor sit amet, consectetur adipiscing elit, sed do eiusmod tempor incididunt ut labore et dolore magna aliqua. Quis ipsum suspendisse ultrices gravida. Risus commodo viverra maecenas accumsan lacus vel facilisis.</p>
        <p>Lorem ipsum dolor sit amet, consectetur adipiscing elit, sed do eiusmod tempor incididunt ut labore et dolore magna aliqua. Quis ipsum suspendisse ultrices gravida. Risus commodo viverra maecenas accumsan lacus vel facilisis. Lorem ipsum dolor sit amet, consectetur adipiscing elit, sed do eiusmod tempor incididunt ut labore et dolore magna aliqua. Quis ipsum suspendisse ultrices gravida. Risus commodo viverra maecenas accumsan lacus vel facilisis. Lorem ipsum dolor sit amet, consectetur adipiscing elit, sed do eiusmod tempor incididunt ut labore et dolore magna aliqua. Quis ipsum suspendisse ultrices gravida. Risus commodo viverra maecenas accumsan lacus vel facilisis.</p>
      </div>
    </section>

    <section class="spine">
      <div class="spine-title title-display">DISTANCE RACING BLUEPRINTS</div>
      <div class="spine-author">AUTHOR NAME</div>
    </section>

    <section class="front">
      <div class="author">AUTHOR NAME</div>
      <h1 class="front-title title-display">
        <span class="blue">DISTANCE</span>
        <span class="blue">RACING</span>
        <span class="black">BLUEPRINTS</span>
      </h1>
      <p class="front-sub sub">An in-depth manual for <em>achieving your peak race day</em><br>featuring schedules, counsel and target-reaching pointers</p>
      <div class="photo" role="img" aria-label="Photo of a group of race runners with bibs crossing a red finish-line tape, a joyful woman in a light blue top at the centre with arms raised"></div>
    </section>
  </div>
</body>
</html>
```